Waste management company seeks a new website design

We need a website design for an environmental services company called 'Laanemetsa Haldusgrupp.' We manage waste collection and recycling for 100K+ households and businesses across Estonia. Please use logos and colors from attached CVI file. The design should be extensively usable for our self-service portal and have a mobile-first approach as it will be turned into an app in the future. The new website should highlight our commitment to sustainability and provide easy access to our services with a clean, modern design. UX inspiration from https://ruvako.eu/et-ee/

```html
<!DOCTYPE html>
<html lang="en">
<head>
<meta charset="utf-8">
<title>Laanemetsa Haldusgrupp – Committed To A Greener Estonia</title>
<link href="https://fonts.googleapis.com/css2?family=Montserrat:wght@400;500;600;700&display=swap" rel="stylesheet">
<style>
:root{
  --lime:#ccdc2a;
  --lime-soft:#f3f6d6;
  --lime-tint:#f6f9dc;
  --brown:#7b6b5f;
  --brown-dark:#5f5148;
  --title:#6c5d52;
  --text:#4d4d4d;
  --muted:#7a7a7a;
  --white:#ffffff;
  --line:#e9e9e9;
}
*{box-sizing:border-box;margin:0;padding:0}
html,body{width:1200px;height:4619px;overflow:hidden}
body{position:relative;font-family:"Montserrat",sans-serif;color:var(--text);background:var(--white)}
.abs{position:absolute}
a{color:inherit;text-decoration:none}
.btn{position:absolute;display:flex;align-items:center;justify-content:center;background:var(--lime);color:#2c2c2c;font-weight:700;font-size:14px;border-radius:20px}
.ornament{position:absolute;width:140px;height:26px;left:50%;transform:translateX(-50%)}
.section-title{position:absolute;left:0;width:1200px;text-align:center;font-weight:700;font-size:40px;color:var(--title)}
.photo{position:absolute;overflow:hidden}

/* hero */
.hero{position:absolute;left:0;top:0;width:1200px;height:762px;background:linear-gradient(160deg,#3f4a22 0%,#2b3019 45%,#4a3c22 100%)}
.hero-curve{position:absolute;left:0;top:660px;width:1200px;height:104px}
.brand{position:absolute;left:88px;top:8px;width:150px;text-align:center;color:var(--white);font-weight:700;font-size:14px;line-height:17px}
.brand-dot{width:34px;height:34px;border-radius:50%;background:var(--white);margin:0 auto 4px}
.contact-item{position:absolute;top:24px;color:var(--white);font-size:12px;line-height:16px;display:flex;gap:10px}
.contact-item b{display:block;color:var(--lime);font-weight:600;font-size:11px}
.contact-sep{position:absolute;top:18px;width:1px;height:56px;background:rgba(255,255,255,.35)}
.nav{position:absolute;top:104px;left:270px;display:flex;gap:34px;color:var(--white);font-size:12px;font-weight:600}
.hero h1{position:absolute;left:0;top:260px;width:1200px;text-align:center;color:var(--white);font-size:68px;line-height:66px;font-weight:700}
.hero p{position:absolute;left:370px;top:412px;width:460px;text-align:center;color:var(--white);font-size:13px;line-height:17px;font-weight:500}

/* about */
.about-text{position:absolute;left:680px;top:860px;width:420px}
.about-text h2{font-size:40px;line-height:42px;color:var(--title);font-weight:700}
.kicker{color:var(--lime);font-weight:600;font-size:16px;margin-top:14px}
.para{font-size:13px;line-height:31px;color:var(--text);margin-top:10px}

/* services */
.services{position:absolute;left:93px;top:1482px;width:1014px;height:380px;border:1px solid var(--line);border-radius:10px;display:flex}
.service{position:relative;flex:1;text-align:center;border-right:1px solid var(--line)}
.service:last-child{border-right:none}
.service.active{background:var(--brown)}
.step{position:absolute;top:-12px;left:50%;transform:translateX(-50%);background:var(--brown-dark);color:var(--white);font-size:12px;font-weight:600;padding:4px 16px;border-radius:12px}
.active .step{background:var(--lime);color:var(--white)}
.s-icon{width:104px;height:104px;border-radius:50%;background:var(--lime-soft);margin:56px auto 0}
.active .s-icon{background:#a3a83a}
.service h3{font-size:19px;line-height:22px;font-weight:500;color:var(--title);margin:36px 12px 0;height:46px}
.active h3{color:var(--lime)}
.service p{font-size:11px;line-height:15px;color:var(--muted);margin:10px 34px 0;height:70px}
.active p{color:var(--white)}
.read{font-size:14px;color:var(--lime);display:inline-flex;align-items:center;gap:8px;margin-top:12px}

/* cards */
.card{position:absolute;background:var(--white);border-radius:16px;box-shadow:0 6px 24px rgba(0,0,0,.09);text-align:center}
.card .date{font-size:25px;color:#555;margin-top:30px}
.card .body{font-size:17px;line-height:26px;color:#666;margin:12px 26px 0}

/* testimonials */
.testi-band{position:absolute;left:0;top:2849px;width:1200px;height:551px;background:var(--lime-tint)}
.testi{position:absolute;top:3026px;width:482px;height:252px;background:var(--white);border-radius:22px}
.stars{position:absolute;left:34px;top:38px;color:#e7a919;font-size:14px;letter-spacing:1px}
.quote{position:absolute;left:34px;top:70px;width:210px;font-size:11px;line-height:16px;color:#666}
.who{position:absolute;left:34px;top:180px;font-size:12px;font-weight:600;color:#555}
.avatar{position:absolute;right:36px;top:52px;width:164px;height:164px;border-radius:50%;border:4px solid var(--brown-dark);background:linear-gradient(135deg,#e8c27a,#8a9a4a)}
.qbadge{position:absolute;right:36px;top:38px;width:56px;height:56px;border-radius:50%;background:var(--lime);border:4px solid var(--white);color:#222;font-weight:700;font-size:34px;line-height:56px;text-align:center}
.arrow-btn{position:absolute;top:3130px;width:44px;height:44px;border-radius:50%;border:1.5px solid #555}

/* cta */
.cta{position:absolute;left:0;top:4004px;width:1200px;height:242px;background:var(--brown)}
.cta h2{position:absolute;left:90px;top:40px;color:var(--white);font-size:40px;line-height:42px;font-weight:700}
.cta p{position:absolute;left:90px;top:136px;color:var(--white);font-size:13px}

/* footer */
.f-col h4{font-size:18px;font-weight:600;color:var(--title);border-left:2px solid var(--title);padding-left:8px;line-height:18px}
.f-col ul{list-style:none;margin-top:14px;padding-left:12px}
.f-col li{font-size:12px;line-height:22px;color:var(--muted)}
.f-contact li{display:flex;align-items:center;gap:12px;line-height:18px;margin-bottom:18px}
.social{position:absolute;top:4422px;width:38px;height:38px;border-radius:50%;background:#e4e4e4}
.social.first{background:var(--brown-dark)}
</style>
</head>
<body>

<!-- Hero -->
<header class="hero" role="img" aria-label="Volunteers in high-visibility vests collecting litter in an autumn forest">
  <div class="brand"><div class="brand-dot"></div>Eesti<br>Laanemetsa Haldusgrupp</div>

  <div class="contact-sep" style="left:310px"></div>
  <div class="contact-item" style="left:318px">
    <svg width="22" height="22" viewBox="0 0 24 24" fill="none" stroke="#fff" stroke-width="1.6"><path d="M5 3h4l2 5-3 2a11 11 0 0 0 6 6l2-3 5 2v4a2 2 0 0 1-2 2A17 17 0 0 1 3 5a2 2 0 0 1 2-2z"/></svg>
    <div><b>Email :</b>info@laanemetsa.ee</div>
  </div>
  <div class="contact-sep" style="left:528px"></div>
  <div class="contact-item" style="left:538px">
    <svg width="26" height="20" viewBox="0 0 26 20" fill="none" stroke="#fff" stroke-width="1.6"><rect x="1" y="1" width="24" height="18" rx="1"/><path d="M1 1l12 10L25 1"/></svg>
    <div><b>Phone :</b>+(372)-555-0142</div>
  </div>
  <div class="contact-sep" style="left:722px"></div>
  <div class="contact-item" style="left:752px">
    <svg width="18" height="24" viewBox="0 0 18 24" fill="none" stroke="#fff" stroke-width="1.6"><path d="M9 23s8-8 8-14A8 8 0 0 0 1 9c0 6 8 14 8 14z"/><circle cx="9" cy="9" r="3"/></svg>
    <div><b>Location :</b>Registered office: Metsa tee<br>14 Estonia</div>
  </div>
  <a class="btn" style="left:988px;top:29px;width:121px;height:37px;font-size:13px" href="#">Get a Quote</a>

  <nav class="nav"><a href="#">Home</a><a href="#">For a home customer</a><a href="#">For a business customer</a><a href="#">Client support</a><a href="#">About</a><a href="#" style="margin-left:8px">Come to work!</a></nav>

  <svg class="ornament" style="top:224px" viewBox="0 0 140 26"><path d="M0 13h44M96 13h44" stroke="#fff" stroke-dasharray="2 3"/><circle cx="70" cy="13" r="10" fill="none" stroke="#fff" stroke-width="2"/></svg>
  <h1>Committed To A<br>Greener Estonia</h1>
  <p>Efficient waste collection and recycling for over 100,000 households and businesses.</p>
  <a class="btn" style="left:515px;top:466px;width:170px;height:40px" href="#">Get Started Now</a>

  <svg class="hero-curve" viewBox="0 0 1200 104" preserveAspectRatio="none"><path d="M0 104V92C300 10 900 -20 1200 70V104z" fill="#fff"/></svg>
</header>

<!-- About -->
<section>
  <div class="photo" role="img" aria-label="Volunteers bagging litter beside a stream" style="left:120px;top:822px;width:235px;height:174px;border-radius:80px 10px 10px 60px;background:linear-gradient(135deg,#6b7c4a,#3e4a2c)"></div>
  <div class="photo" role="img" aria-label="Workers in safety vests raking autumn leaves" style="left:163px;top:1010px;width:192px;height:240px;border-radius:10px 10px 10px 90px;background:linear-gradient(160deg,#c9a24a,#6c5a2c)"></div>
  <div class="photo" role="img" aria-label="Worker in a yellow vest collecting rubbish bags" style="left:368px;top:843px;width:274px;height:386px;border-radius:10px 190px 190px 10px;background:linear-gradient(150deg,#8a8a4a,#3b3a2a)"></div>
  <svg class="abs" style="left:462px;top:995px" width="84" height="84" viewBox="0 0 84 84"><circle cx="42" cy="42" r="42" fill="#ccdc2a"/><path d="M34 26v32l26-16z" fill="#fff"/></svg>

  <svg class="abs" style="left:680px;top:848px" width="140" height="26" viewBox="0 0 140 26"><path d="M0 13h34M70 13h34" stroke="#ccdc2a"/><circle cx="52" cy="13" r="10" fill="none" stroke="#ccdc2a" stroke-width="2"/></svg>
  <div class="about-text" style="top:880px">
    <h2>About Laanemetsa<br>Haldusgrupp</h2>
    <div class="kicker">Mission and Vision</div>
    <p class="para">At Laanemetsa Haldusgrupp, our mission is to provide exceptional waste management and recycling services that contribute to a sustainable and clean environment for all. We envision a future where waste is minimized, resources are conserved, and every community plays an active role in protecting our planet.</p>
  </div>
  <a class="btn" style="left:680px;top:1205px;width:133px;height:38px" href="#">Learn More</a>
</section>

<!-- Services -->
<section>
  <svg class="ornament" style="top:1346px" viewBox="0 0 140 26"><path d="M10 13h44M86 13h44" stroke="#ccdc2a"/><circle cx="70" cy="13" r="10" fill="none" stroke="#ccdc2a" stroke-width="2"/></svg>
  <h2 class="section-title" style="top:1374px">Our Services</h2>
  <div class="services">
    <div class="service"><span class="step">Step 01</span><div class="s-icon"></div><h3>Waste stations</h3><p>Comprehensive recycling solutions for paper, plastic, glass, and metal.</p><a class="read" href="#">Read More <svg width="48" height="8"><path d="M0 4h46M42 1l4 3-4 3" stroke="#ccdc2a" fill="none"/></svg></a></div>
    <div class="service active"><span class="step">Step 02</span><div class="s-icon"></div><h3>Services for business customers</h3><p>Reliable waste collection services for residential and commercial clients.</p><a class="read" href="#">Read More <svg width="48" height="8"><path d="M0 4h46M42 1l4 3-4 3" stroke="#ccdc2a" fill="none"/></svg></a></div>
    <div class="service"><span class="step">Step 03</span><div class="s-icon"></div><h3>Services for private customers</h3><p>Safe and responsible disposal of hazardous materials.</p><a class="read" href="#">Read More <svg width="48" height="8"><path d="M0 4h46M42 1l4 3-4 3" stroke="#ccdc2a" fill="none"/></svg></a></div>
    <div class="service"><span class="step">Step 04</span><div class="s-icon"></div><h3>Roads and streets</h3><p>Expert advice on waste management &amp; sustainability practices.</p><a class="read" href="#">Read More <svg width="48" height="8"><path d="M0 4h46M42 1l4 3-4 3" stroke="#ccdc2a" fill="none"/></svg></a></div>
  </div>
</section>

<!-- Commitment -->
<section>
  <svg class="abs" style="left:181px;top:1978px" width="140" height="26" viewBox="0 0 140 26"><path d="M0 13h34M70 13h34" stroke="#ccdc2a"/><circle cx="52" cy="13" r="10" fill="none" stroke="#ccdc2a" stroke-width="2"/></svg>
  <div class="about-text" style="left:181px;top:2012px;width:380px">
    <h2>Our Commitment<br>to Sustainability</h2>
    <p class="para" style="margin-top:20px">At Laanemetsa Haldusgrupp, sustainability is at the core of everything we do. From our advanced recycling processes to our community outreach programs, we are dedicated to protecting the environment and promoting a greener future for Estonia.</p>
  </div>
  <a class="btn" style="left:181px;top:2318px;width:133px;height:38px" href="#">Learn More</a>

  <div class="photo" role="img" aria-label="Volunteers picking up litter in autumn woods" style="left:666px;top:1963px;width:177px;height:224px;border-radius:90px 90px 10px 10px;background:linear-gradient(160deg,#c9a84e,#6f6a46)"></div>
  <div class="photo" role="img" aria-label="Volunteers holding a rubbish bag outdoors" style="left:859px;top:1963px;width:217px;height:163px;border-radius:10px 90px 90px 10px;background:linear-gradient(140deg,#9aa06a,#b88a4a)"></div>
  <div class="photo" role="img" aria-label="Team in green shirts celebrating next to a wheelie bin" style="left:626px;top:2199px;width:217px;height:165px;border-radius:90px 10px 10px 90px;background:linear-gradient(140deg,#5e9a4a,#2f5a30)"></div>
  <div class="photo" role="img" aria-label="Volunteer kneeling to clear debris from the ground" style="left:861px;top:2138px;width:176px;height:226px;border-radius:10px 10px 90px 90px;background:linear-gradient(160deg,#6a6a52,#2e2c24)"></div>
</section>

<!-- Emergency notifications -->
<section>
  <svg class="ornament" style="top:2463px" viewBox="0 0 140 26"><path d="M10 13h44M86 13h44" stroke="#ccdc2a"/><circle cx="70" cy="13" r="10" fill="none" stroke="#ccdc2a" stroke-width="2"/></svg>
  <h2 class="section-title" style="top:2501px">Emergency Notifications</h2>
  <article class="card" style="left:246px;top:2580px;width:333px;height:168px"><div class="date">14.12.2023</div><div class="body">Dear customers!<br>From 01.01.2024, Tallinn customer service (Kaare 8,</div></article>
  <article class="card" style="left:619px;top:2580px;width:334px;height:168px"><div class="date">10.05.2022</div><div class="body">Customer service in Viljandi is open one day a week – Friday.</div></article>
</section>

<!-- Testimonials -->
<section>
  <div class="testi-band"></div>
  <svg class="ornament" style="top:2906px" viewBox="0 0 140 26"><path d="M10 13h44M86 13h44" stroke="#ccdc2a"/><circle cx="70" cy="13" r="10" fill="none" stroke="#ccdc2a" stroke-width="2"/></svg>
  <h2 class="section-title" style="top:2942px">What Our Customers Say</h2>
  <div class="arrow-btn" style="left:35px"><svg width="44" height="44" viewBox="0 0 44 44"><path d="M25 14l-8 8 8 8" stroke="#555" stroke-width="1.6" fill="none"/></svg></div>
  <div class="arrow-btn" style="left:1118px"><svg width="44" height="44" viewBox="0 0 44 44"><path d="M19 14l8 8-8 8" stroke="#555" stroke-width="1.6" fill="none"/></svg></div>

  <article class="testi" style="left:93px">
    <div class="stars">★★★★★</div>
    <p class="quote">"Laanemetsa Haldusgrupp has significantly improved our waste management processes. Their services are efficient and reliable."</p>
    <div class="who">Kristi Tamm</div>
    <div class="avatar" role="img" aria-label="Customer portrait photo"></div>
    <div class="qbadge">”</div>
  </article>
  <article class="testi" style="left:621px">
    <div class="stars">★★★★★</div>
    <p class="quote">"We appreciate their commitment to sustainability and the environment. Their recycling programs are top-notch."</p>
    <div class="who">Marko Saar</div>
    <div class="avatar" role="img" aria-label="Customer portrait photo" style="background:linear-gradient(135deg,#c98a4a,#5a7a5a)"></div>
    <div class="qbadge">”</div>
  </article>
  <a class="btn" style="left:515px;top:3312px;width:170px;height:37px" href="#">View All Reviews</a>
</section>

<!-- Latest news -->
<section>
  <svg class="ornament" style="top:3500px" viewBox="0 0 140 26"><path d="M10 13h44M86 13h44" stroke="#ccdc2a"/><circle cx="70" cy="13" r="10" fill="none" stroke="#ccdc2a" stroke-width="2"/></svg>
  <h2 class="section-title" style="top:3536px">Latest news</h2>
  <article class="card" style="left:90px;top:3611px;width:317px;height:241px"><div class="date" style="margin-top:48px">14.12.2023</div><div class="body" style="height:78px">Change in the opening hours of customer service in Tallinn</div><a class="read" href="#">Read More <svg width="48" height="8"><path d="M0 4h46M42 1l4 3-4 3" stroke="#ccdc2a" fill="none"/></svg></a></article>
  <article class="card" style="left:440px;top:3611px;width:317px;height:241px"><div class="date" style="margin-top:48px">14.12.2023</div><div class="body" style="height:78px">Change in VAT rate from 01.01.2024</div><a class="read" href="#">Read More <svg width="48" height="8"><path d="M0 4h46M42 1l4 3-4 3" stroke="#ccdc2a" fill="none"/></svg></a></article>
  <article class="card" style="left:789px;top:3611px;width:318px;height:241px"><div class="date" style="margin-top:48px">18.12.2018</div><div class="body" style="height:78px">Invoicing changes</div><a class="read" href="#">Read More <svg width="48" height="8"><path d="M0 4h46M42 1l4 3-4 3" stroke="#ccdc2a" fill="none"/></svg></a></article>
</section>

<!-- CTA -->
<section class="cta">
  <h2>Simplify Your<br>Waste Management</h2>
  <p>Easily schedule pickups, track recycling, and access support.</p>
  <a class="btn" style="left:90px;top:169px;width:131px;height:37px" href="#">Learn More</a>
</section>
<div class="photo" role="img" aria-label="Smiling woman holding two recycling bins" style="left:798px;top:3893px;width:332px;height:353px;border-radius:160px 160px 0 0;background:linear-gradient(180deg,#e2b46a 0%,#3f8a5a 55%,#d9d0c4 100%)"></div>

<!-- Footer -->
<footer>
  <div class="abs" style="left:90px;top:4297px;width:180px;text-align:center;color:var(--title);font-weight:500;font-size:19px;line-height:24px">
    <div style="width:46px;height:46px;border-radius:50%;background:var(--title);margin:0 auto 8px"></div>Eesti<br>Laanemetsa Haldusgrupp
  </div>
  <a class="social first" style="left:89px" href="#" aria-label="Social profile"></a>
  <a class="social" style="left:137px" href="#" aria-label="Social profile"></a>
  <a class="social" style="left:182px" href="#" aria-label="Social profile"></a>
  <a class="social" style="left:229px" href="#" aria-label="Social profile"></a>

  <div class="abs" style="left:342px;top:4300px;width:1px;height:190px;background:var(--line)"></div>
  <div class="abs" style="left:570px;top:4300px;width:1px;height:190px;background:var(--line)"></div>
  <div class="abs" style="left:820px;top:4300px;width:1px;height:190px;background:var(--line)"></div>

  <div class="abs f-col" style="left:377px;top:4322px">
    <h4>Quick Links</h4>
    <ul><li>Home</li><li>For a home customer</li><li>For a business customer</li><li>Client support</li><li>About</li><li>Come to work!</li></ul>
  </div>
  <div class="abs f-col f-contact" style="left:605px;top:4322px">
    <h4>Contact Us</h4>
    <ul style="margin-top:24px">
      <li><svg width="12" height="12" viewBox="0 0 24 24" fill="#ccdc2a"><path d="M5 3h4l2 5-3 2a11 11 0 0 0 6 6l2-3 5 2v4a2 2 0 0 1-2 2A17 17 0 0 1 3 5a2 2 0 0 1 2-2z"/></svg>+(372)-555-0142</li>
      <li><svg width="12" height="10" viewBox="0 0 26 20" fill="#ccdc2a"><rect width="26" height="20" rx="2"/></svg>info@laanemetsa.ee</li>
      <li><svg width="10" height="14" viewBox="0 0 18 24" fill="#ccdc2a"><path d="M9 24s9-9 9-15A9 9 0 0 0 0 9c0 6 9 15 9 15z"/></svg>Registered office: Metsa tee<br>14 Estonia</li>
    </ul>
  </div>
  <div class="abs f-col" style="left:856px;top:4322px;width:251px">
    <h4>Subscribe Newsletter</h4>
    <p style="font-size:11px;line-height:17px;color:var(--muted);margin:14px 0 0 12px">Subscribe newsletter for the latest offers and news</p>
  </div>
  <div class="abs" style="left:856px;top:4413px;width:251px;height:43px;border-radius:22px;box-shadow:0 4px 14px rgba(0,0,0,.08);background:var(--white)">
    <span class="abs" style="left:26px;top:14px;font-size:10px;color:#aaa">Enter Email...</span>
    <span class="abs" style="right:0;top:0;width:54px;height:43px;border-radius:0 22px 22px 0;background:var(--lime)"><svg width="54" height="43"><path d="M18 21.5h18M31 17l5 4.5-5 4.5" stroke="#fff" stroke-width="1.6" fill="none"/></svg></span>
  </div>

  <div class="abs" style="left:90px;top:4548px;width:1017px;height:1px;background:var(--line)"></div>
  <p class="abs" style="left:90px;top:4576px;font-size:11px;color:#666">Copyrights 2024, Laanemetsa Haldusgrupp. All Rights Reserved</p>
  <p class="abs" style="left:893px;top:4576px;font-size:11px;color:#666">Privacy Policy | Terms &amp; Conditions</p>
  <a class="abs" href="#" aria-label="Back to top" style="left:1131px;top:4537px;width:40px;height:40px;border-radius:50%;background:var(--lime)"><svg width="40" height="40"><path d="M16 22l4-4 4 4" stroke="#fff" stroke-width="1.6" fill="none"/></svg></a>
</footer>

</body>
</html>
```